Counseling Practice Business Card

I need a professional looking business card incorporating my new logo that was just completed. Card needs to incorporate my name and title, description of my specialty, my address, my phone number, my fax number, my email and my website URL. I need to be able to choose design on/with different paper colors and textures.
I do not have a lot of business card ideas so I am open to anything but I want bold,sharp, clear card without additional designs other than my logo (see attached file info). I am open to different color backgrounds or paper colors including black. I do not like traditional brackets around area codes in phone number or dashes between numbers in phone number. Am open to other ways of presenting including periods between numbers as appropriate. I do not know enough to know what I like yet but I want card to coordinate and work together with my logo. My practice emphasizes natural mental health interventions so any use of color (with background paper color or the blue and green in my logo) that elicits nature is nice. In addition to black, any natural brown or wood looking background might be desirable also. Most of the offerings so far look very similar and boring.

Target Market(s)

Potential therapy clients and other professionals

Contact Information for Business Card

Card information:
Gerald M. Whitcombe, Ph.D.
Licensed Clinical Psychologist
Integrative Health Coach
4812 Marlowe Ridge Blvd SE
Suite 310
Duluth, GA 30096
(770) 415-2983 phone
(770) 581-4096 fax
drgeraldwhitcombe@quillmarsh.net
brightfernwellness.net

Font styles to use
Serif
Sans Serif
Other font styles liked:
• anything that you think looks crisp, clear and easily readable

Requirements
Must have
• Any color used should coordinate with my logo design (see attached files).
• Card should be printed horizontally so top and bottom are longest sides of rectangle.
• Background color or paper color should complement and highlight logo. Do not like a white background. black, grey, brown or any color my logo would blend well with.
Nice to have
• I would like designer to utilize color to highlight letters/name or phone-fax-web symbols.
• Bottom edge of card could be highlighted if appropriate to an idea.
Should not have
• I would NOT want the card to have a pure white background at all.
• No clear cards.
• Cards should be oriented with long sides on bottom and top, NOT sides. DO NOT LIKE THIS THIN TALL ORIENTATION.

```html
<!DOCTYPE html>
<html lang="en">
<head>
<meta charset="utf-8">
<title>Brightfern Wellness – Business Card</title>
<link rel="stylesheet" href="https://fonts.googleapis.com/css2?family=Source+Sans+3:wght@400;700&display=swap">
<style>
  :root {
    --backdrop: #3b3b3d;
    --card-black: #161719;
    --card-ink: #232427;
    --emboss: #2a2b2e;
    --fern-green: #0f8a45;
    --sky-blue: #2a7fd0;
    --logo-blue: #3a8ad6;
    --text-light: #d9dadc;
    --text-white: #ffffff;
    --divider: #4a4b4f;
  }
  * { margin: 0; padding: 0; box-sizing: border-box; }
  html, body {
    width: 1200px; height: 840px; overflow: hidden;
    background: var(--backdrop);
    font-family: "Source Sans 3", Arial, sans-serif;
  }
  .canvas { position: relative; width: 1200px; height: 840px; }
  .card {
    position: absolute; left: 290px; width: 620px; height: 354px;
    background: linear-gradient(160deg, var(--card-ink), var(--card-black));
    overflow: hidden;
    box-shadow: 0 8px 24px rgba(0,0,0,0.35);
  }
  .card--front { top: 36px; }
  .card--back { top: 450px; }

  .front-mark {
    position: absolute; inset: 0;
    display: flex; align-items: center; justify-content: center;
    font-size: 52px; font-weight: 700; color: var(--emboss);
    letter-spacing: 1px;
  }

  .back-band { position: absolute; left: 0; top: 0; width: 620px; height: 354px; }

  .identity {
    position: absolute; right: 22px; top: 14px; text-align: right;
    color: var(--text-white);
  }
  .identity__name {
    font-size: 19px; font-weight: 700; text-transform: uppercase; letter-spacing: 0.3px;
  }
  .identity__title { font-size: 14px; font-weight: 400; line-height: 17px; }

  .brand {
    position: absolute; left: 44px; top: 262px;
    display: flex; align-items: center; gap: 10px;
  }
  .brand__dot { width: 16px; height: 16px; border-radius: 50%; background: var(--fern-green); }
  .brand__name { font-size: 28px; font-weight: 700; color: var(--logo-blue); }

  .divider {
    position: absolute; left: 318px; top: 160px; width: 1px; height: 170px;
    background: var(--divider);
  }

  .contact {
    position: absolute; left: 336px; top: 168px;
    color: var(--text-light); font-size: 13.5px; line-height: 18px;
  }
  .contact__address { margin-bottom: 6px; }
  .contact__row { display: flex; align-items: center; gap: 7px; }
  .contact__icon { width: 12px; height: 12px; flex: none; }
</style>
</head>
<body>
<main class="canvas">

  <section class="card card--front" aria-label="Card front">
    <div class="front-mark">Brightfern Wellness</div>
  </section>

  <section class="card card--back" aria-label="Card back">
    <svg class="back-band" viewBox="0 0 620 354" aria-hidden="true">
      <path d="M0 0 H620 V112 C440 96 220 110 0 158 Z" fill="var(--fern-green)"/>
      <path d="M0 158 C220 110 440 96 620 112 V124 C440 106 220 118 0 164 Z" fill="var(--sky-blue)"/>
    </svg>

    <div class="identity">
      <div class="identity__name">Gerald M. Whitcombe, Ph.D.</div>
      <div class="identity__title">Licensed Clinical Psychologist</div>
      <div class="identity__title">Integrative Health Coach</div>
    </div>

    <div class="brand">
      <span class="brand__dot"></span>
      <span class="brand__name">Brightfern Wellness</span>
    </div>

    <div class="divider"></div>

    <div class="contact">
      <div class="contact__address">
        4812 Marlowe Ridge Blvd SE<br>
        Suite 310<br>
        Duluth, GA 30096
      </div>
      <div class="contact__row">
        <svg class="contact__icon" viewBox="0 0 12 12" aria-label="Phone"><path d="M2.5 1 L4.5 1 L5.2 3.6 L4 4.5 C4.6 6 5.9 7.4 7.5 8 L8.4 6.8 L11 7.5 L11 9.5 C11 10.3 10.3 11 9.5 11 C5 11 1 7 1 2.5 C1 1.7 1.7 1 2.5 1 Z" fill="var(--sky-blue)"/></svg>
        (770) 415-2983
      </div>
      <div class="contact__row">
        <svg class="contact__icon" viewBox="0 0 12 12" aria-label="Fax"><rect x="3" y="1" width="6" height="3" fill="var(--sky-blue)"/><rect x="1" y="4.5" width="10" height="5" rx="1" fill="var(--sky-blue)"/><rect x="3" y="8" width="6" height="3" fill="var(--text-light)"/></svg>
        (770) 581-4096
      </div>
      <div class="contact__row">
        <svg class="contact__icon" viewBox="0 0 12 12" aria-label="Email"><rect x="0.5" y="2.5" width="11" height="7.5" rx="1" fill="var(--sky-blue)"/><path d="M1 3 L6 7 L11 3" stroke="var(--card-black)" stroke-width="1" fill="none"/></svg>
        drgeraldwhitcombe@quillmarsh.net
      </div>
      <div class="contact__row">
        <svg class="contact__icon" viewBox="0 0 12 12" aria-label="Website"><circle cx="6" cy="6" r="5.2" fill="var(--sky-blue)"/><path d="M1 6 H11 M6 1 C3.8 3.5 3.8 8.5 6 11 M6 1 C8.2 3.5 8.2 8.5 6 11" stroke="var(--card-black)" stroke-width="0.8" fill="none"/></svg>
        www.brightfernwellness.net
      </div>
    </div>
  </section>

</main>
</body>
</html>
```